Patent Law

Need to develop a home page for a patent lawyer.

Colors should go with logo, blues...

Company Name- Velun Tresk, PLLC

Company Overview-

I am an Intellectual Property Lawyer and focus on patents, copyrights, trademarks, & trade secrets. I work with small businesses and start ups in the chemical and biotech industries.

Why Us-

I am small firm that can provide large-firm service at a reasonable price. I also can charge flat-fees for entreprenuers in certain practice areas.

Services-
Intellectual Property
Patents
Copyrights
Trademarks
Trade secrets
Healthcare Compliance
Elder law
Wills
Trusts

Website we like-
http://www.quorvantlegal.example/ - within industry!!
http://www.daltrowemiko.example/
http://ulbrixtane.example/
http://thegravelcounsel.example/

Target Market(s)

My customers will be small business, specifically small start-up companies in the chemical and biotech arena.

Industry/Entity Type

Trade

Requirements
Must have
• Colors should go with logo, blues...

```html
<!DOCTYPE html>
<html lang="en">
<head>
<meta charset="utf-8">
<title>Velun Tresk, PLLC — Intellectual Property Law</title>
<link rel="stylesheet" href="https://fonts.googleapis.com/css2?family=Open+Sans:ital,wght@0,400;0,600;0,700;1,400&family=Roboto+Slab:wght@300;400&family=Lato:wght@400;700&display=swap">
<style>
  :root {
    --teal: #1f6079;
    --paper: #f4f4f4;
    --header-bg: #fafafa;
    --ink: #3d3d3d;
    --ink-soft: #555555;
    --heading: #565656;
    --rule: #d2d2d2;
    --white: #ffffff;
    --photo-a: #8a4a22;
    --photo-b: #c98a55;
  }
  * { box-sizing: border-box; margin: 0; padding: 0; }
  html, body { width: 1200px; height: 846px; overflow: hidden; }
  body { position: relative; background: var(--paper); font-family: "Open Sans", Arial, sans-serif; color: var(--ink); }

  .site-header { position: absolute; left: 0; top: 0; width: 1200px; height: 78px; background: var(--header-bg); border-bottom: 1px solid #e4e4e4; }
  .brand { position: absolute; left: 240px; top: 32px; display: flex; align-items: center; gap: 6px; }
  .brand-dot { width: 10px; height: 10px; border-radius: 50%; background: var(--teal); flex: none; }
  .brand-name { font-family: "Roboto Slab", Georgia, serif; font-size: 10px; font-weight: 400; color: var(--teal); letter-spacing: .3px; white-space: nowrap; }

  .main-nav { position: absolute; left: 393px; top: 0; display: flex; height: 56px; }
  .main-nav a { display: block; height: 56px; padding: 0 10px; margin-right: 0; line-height: 78px; font-family: "Lato", Arial, sans-serif; font-size: 10.5px; color: #2b2b2b; text-decoration: none; white-space: nowrap; }
  .main-nav a.is-active { background: var(--teal); color: var(--white); margin-right: 8px; }

  .header-contact { position: absolute; right: 246px; top: 22px; text-align: right; font-weight: 600; color: #333; }
  .header-contact .phone, .header-contact .map { font-size: 14px; line-height: 17px; display: flex; align-items: center; justify-content: flex-end; gap: 4px; }
  .header-contact svg { fill: var(--teal); }

  .hero-band { position: absolute; left: 0; top: 78px; width: 1200px; height: 399px; background: var(--teal); }
  .hero-slide { position: absolute; left: 240px; top: 17px; width: 714px; height: 366px; background: linear-gradient(100deg, var(--photo-a) 0%, var(--photo-b) 45%, #6f3f22 75%, #2a2623 100%); }
  .slider-arrow { position: absolute; top: 168px; width: 29px; height: 29px; border-radius: 50%; background: rgba(255,255,255,.55); display: flex; align-items: center; justify-content: center; }
  .slider-arrow.prev { left: 15px; }
  .slider-arrow.next { right: 15px; }

  .info-section { position: absolute; left: 0; top: 477px; width: 1200px; height: 284px; }
  .col { position: absolute; top: 16px; }
  .col h2 { font-family: "Roboto Slab", Georgia, serif; font-weight: 300; font-size: 17px; color: var(--heading); margin-bottom: 5px; }
  .col p { font-size: 10.2px; line-height: 13.4px; color: var(--ink); }
  .col p + p { margin-top: 13.4px; }
  .col a { color: var(--teal); text-decoration: none; }
  .why-us { left: 240px; width: 228px; }
  .services { left: 506px; }
  .services ul { list-style: none; }
  .services li { font-size: 10.2px; line-height: 13.2px; color: var(--ink); display: flex; align-items: center; gap: 4px; }
  .services li::before { content: ""; border-left: 3px solid var(--teal); border-top: 3px solid transparent; border-bottom: 3px solid transparent; }
  .contact-info { left: 725px; }
  .contact-info h3 { font-size: 11.5px; font-weight: 700; color: var(--teal); line-height: 16px; }
  .contact-info p + h3 { margin-top: 3px; }

  .newsletter-box { position: absolute; left: 240px; top: 669px; width: 714px; height: 73px; border: 1px solid #c9c9c9; background: #f8f8f8; }
  .quote-mark { position: absolute; left: 28px; top: 6px; font-family: "Roboto Slab", Georgia, serif; font-size: 62px; color: #8d8d8d; line-height: 62px; }
  .quote-text { position: absolute; left: 79px; top: 20px; width: 290px; font-family: "Roboto Slab", Georgia, serif; font-style: italic; font-size: 10px; line-height: 14px; color: var(--ink-soft); }
  .quote-dots { position: absolute; left: 357px; top: 57px; display: flex; gap: 3px; }
  .quote-dots span { width: 8px; height: 8px; border-radius: 50%; background: #b9b9b9; }
  .quote-dots span.is-active { background: var(--teal); }
  .box-divider { position: absolute; left: 399px; top: 10px; width: 1px; height: 53px; background: var(--rule); }
  .email-field { position: absolute; left: 420px; top: 24px; width: 224px; height: 24px; border: 1px solid #c6c6c6; background: var(--white); display: flex; align-items: center; padding-left: 8px; gap: 6px; font-family: "Roboto Slab", Georgia, serif; font-style: italic; font-size: 10px; color: #999; }
  .subscribe-btn { position: absolute; left: 649px; top: 24px; width: 53px; height: 24px; background: var(--teal); color: var(--white); font-family: "Roboto Slab", Georgia, serif; font-style: italic; font-size: 10px; display: flex; align-items: center; justify-content: center; }

  .site-footer { position: absolute; left: 0; top: 761px; width: 1200px; height: 85px; background: var(--teal); }
  .copyright { position: absolute; left: 240px; top: 36px; font-size: 10.5px; color: var(--white); }
  .footer-brand { position: absolute; right: 246px; top: 58px; display: flex; align-items: center; gap: 6px; }
  .footer-brand .brand-name { color: var(--white); }
  .footer-brand .brand-dot { background: var(--white); }
</style>
</head>
<body>

<header class="site-header">
  <div class="brand">
    <span class="brand-dot"></span>
    <span class="brand-name">VELUN TRESK, PLLC</span>
  </div>
  <nav class="main-nav">
    <a class="is-active" href="#">Home</a>
    <a href="#">About Velun</a>
    <a href="#">Practice Area</a>
    <a href="#">Lawyers</a>
    <a href="#">Case Study</a>
    <a href="#">Contact Us</a>
  </nav>
  <div class="header-contact">
    <div class="phone">
      <svg width="11" height="11" viewBox="0 0 24 24"><path d="M6.6 10.8a15.1 15.1 0 0 0 6.6 6.6l2.2-2.2c.3-.3.7-.4 1-.2 1.1.4 2.3.6 3.6.6.6 0 1 .4 1 1V20c0 .6-.4 1-1 1C10.6 21 3 13.4 3 4c0-.6.4-1 1-1h3.5c.6 0 1 .4 1 1 0 1.3.2 2.5.6 3.6.1.3 0 .7-.2 1z"/></svg>
      123.456.7894
    </div>
    <div class="map">
      <svg width="8" height="12" viewBox="0 0 16 24"><path d="M8 0C3.6 0 0 3.6 0 8c0 6 8 16 8 16s8-10 8-16c0-4.4-3.6-8-8-8zm0 11a3 3 0 1 1 0-6 3 3 0 0 1 0 6z"/></svg>
      Our Map
    </div>
  </div>
</header>

<section class="hero-band">
  <div class="hero-slide" role="img" aria-label="Photo of a lawyer in a suit meeting a client across a desk in a wood-panelled office">
    <div class="slider-arrow prev"><svg width="10" height="12" viewBox="0 0 10 12"><path d="M7 1 2 6l5 5" stroke="#7a3a1c" stroke-width="2.4" fill="none"/></svg></div>
    <div class="slider-arrow next"><svg width="10" height="12" viewBox="0 0 10 12"><path d="M3 1l5 5-5 5" stroke="#3a2a22" stroke-width="2.4" fill="none"/></svg></div>
  </div>
</section>

<section class="info-section">
  <div class="col why-us">
    <h2>Why Us?</h2>
    <p>Lorem Ipsum is that it has a more-or-less normal distribution of letters, as opposed to using 'Content here, content here', making it look like readable English.</p>
    <p>Lorem Ipsum is that it has a more-or-less normal distribution of letters, as opposed to using 'Content here, content here', making it look like readable English. <a href="#">Read More</a></p>
  </div>
  <div class="col services">
    <h2>What WE Do?</h2>
    <ul>
      <li>Intellectual Property</li>
      <li>Patents</li>
      <li>Copyrights</li>
      <li>Trademarks</li>
      <li>Trade secrets</li>
      <li>Healthcare Compliance</li>
      <li>Elder law</li>
      <li>Wills</li>
      <li>Trusts</li>
    </ul>
  </div>
  <div class="col contact-info">
    <h2>Contact Info</h2>
    <h3>London Office</h3>
    <p>Address: Lorum Street . ABC 123 Lorum,NYC<br>Phone: 2345 678 12<br>Fax: 12345 678 12</p>
    <h3>Canada Office</h3>
    <p>Address: Lorum Street . ABC 123 Lorum,NYC<br>Phone: 2345 678 12<br>Fax: 12345 678 12</p>
  </div>
</section>

<div class="newsletter-box">
  <div class="quote-mark">&ldquo;</div>
  <p class="quote-text">Mauris fermentum dictum magnased laoreet aliquam telsolor dapibus elementun cursus eleifend, elit...</p>
  <div class="quote-dots"><span class="is-active"></span><span></span><span></span></div>
  <div class="box-divider"></div>
  <div class="email-field">
    <svg width="12" height="9" viewBox="0 0 12 9"><rect x=".5" y=".5" width="11" height="8" fill="none" stroke="#aaa"/><path d="M.5.5 6 5l5.5-4.5" fill="none" stroke="#aaa"/></svg>
    e-mail address
  </div>
  <div class="subscribe-btn">Subscribe</div>
</div>

<footer class="site-footer">
  <p class="copyright">&copy; 2013 Velun Tresk.PLL. All rights reserved.</p>
  <div class="footer-brand">
    <span class="brand-dot"></span>
    <span class="brand-name">VELUN TRESK, PLLC</span>
  </div>
</footer>

</body>
</html>
```